New Webpage for High Class Expert Witness Services Company

We are looking for a minimalist design for a webpage that just has our logo and an entry form offer to connect with one of our Liaisons.
The entry form should just ask for Name, Email, Contact Info and Description of Project.

Company Name is: The Marlowe Crest Advisory Services

Number of Pages Required

1 page

```html
<!DOCTYPE html>
<html lang="en">
<head>
<meta charset="utf-8">
<title>The Marlowe Crest Advisory Services – Contact</title>
<link rel="stylesheet" href="https://fonts.googleapis.com/css2?family=Barlow:wght@400;500&display=swap">
<style>
  :root {
    --bg-deep: #0d0d0d;
    --bg-mid: #1c1c1c;
    --brand-text: #d9d9d9;
    --panel-top: #dcdbd8;
    --panel-mid: #f6f6f4;
    --panel-bottom: #ebebe8;
    --label: #8f8f8f;
    --value: #111111;
    --rule: #b9b9b7;
    --button: #111111;
    --button-text: #ffffff;
    --footer-text: #ffffff;
  }
  * { box-sizing: border-box; margin: 0; padding: 0; }
  html, body { width: 1200px; height: 572px; overflow: hidden; }
  body {
    position: relative;
    font-family: "Barlow", Arial, sans-serif;
    background: var(--bg-deep);
  }
  .backdrop {
    position: absolute; inset: 0;
    background:
      radial-gradient(ellipse 420px 260px at 330px 300px, #2a2e2d 0%, rgba(30,32,32,0.5) 50%, rgba(13,13,13,0) 100%),
      linear-gradient(180deg, var(--bg-mid) 0%, #141414 50%, var(--bg-deep) 100%);
  }
  .brand {
    position: absolute;
    left: 110px; top: 258px; width: 394px;
    text-align: center;
    color: var(--brand-text);
    font-weight: 500;
    font-size: 25px;
    line-height: 30px;
    letter-spacing: 2px;
    text-transform: uppercase;
  }
  .contact-panel {
    position: absolute;
    left: 609px; top: 55px; width: 482px; height: 462px;
    background: linear-gradient(180deg, var(--panel-top) 0%, var(--panel-mid) 55%, var(--panel-bottom) 100%);
  }
  .field {
    position: absolute;
    left: 27px; width: 428px;
    border-bottom: 1px solid var(--rule);
    padding-left: 20px;
  }
  .field-label {
    display: block;
    font-size: 11.5px;
    color: var(--label);
  }
  .field-value {
    display: block;
    margin-top: 9px;
    padding-bottom: 11px;
    font-size: 14px;
    font-weight: 500;
    color: var(--value);
    letter-spacing: 0.3px;
  }
  .field-name { top: 34px; }
  .field-email { top: 116px; }
  .field-phone { top: 202px; }
  .field-project { top: 285px; }
  .send-button {
    position: absolute;
    left: 51px; top: 373px; width: 379px; height: 52px;
    background: var(--button);
    color: var(--button-text);
    border: none;
    font-family: inherit;
    font-size: 15px;
    letter-spacing: 0.5px;
    display: flex; align-items: center; justify-content: center;
  }
  .site-footer {
    position: absolute;
    left: 0; width: 1200px; top: 538px;
    text-align: center;
    color: var(--footer-text);
    font-size: 11.5px;
    font-weight: 500;
  }
</style>
</head>
<body>
  <div class="backdrop" role="img" aria-label="Dark photograph of a person working at a laptop showing a world map dashboard"></div>

  <div class="brand">The Marlowe Crest<br>Advisory Services</div>

  <form class="contact-panel">
    <div class="field field-name">
      <span class="field-label">Name</span>
      <span class="field-value">Evan Hartley</span>
    </div>
    <div class="field field-email">
      <span class="field-label">Email</span>
      <span class="field-value">name@example.com</span>
    </div>
    <div class="field field-phone">
      <span class="field-label">Phone Number</span>
      <span class="field-value">123-456-7890</span>
    </div>
    <div class="field field-project">
      <span class="field-label">Project Discription</span>
      <span class="field-value">type here...</span>
    </div>
    <button type="button" class="send-button">SEND</button>
  </form>

  <footer class="site-footer">© Copyright 2026 | The Marlowe Crest Advisory Services | All Right Reserved</footer>
</body>
</html>
```